Stonebridge Building and Projects business cards

A business card with watermark background (construction work)

Company logo attached

Home improvement projects
House renovations
Bathroom and kitchen renovations
House extensions
New builds and granny flats

Director Omar Haddani
(Phone number)
omar@sbpbuilding.com.au
(Instagram logo) sbp_building

```html
<!DOCTYPE html>
<html lang="en">
<head>
<meta charset="utf-8">
<title>Stonebridge Building and Projects – Business Cards</title>
<link rel="stylesheet" href="https://fonts.googleapis.com/css2?family=Montserrat:wght@400;500;600;700&display=swap">
<style>
  :root {
    --brand-blue: #1f6bb5;
    --brand-blue-deep: #1a5fa3;
    --ink: #2a2a2a;
    --card-white: #ffffff;
    --backdrop: #9a9a9a;
    --divider: #d6d6d6;
  }
  * { box-sizing: border-box; margin: 0; padding: 0; }
  html, body { width: 1200px; height: 800px; overflow: hidden; }
  body {
    background: var(--backdrop);
    font-family: "Montserrat", sans-serif;
    display: flex;
    align-items: center;
    justify-content: center;
    gap: 40px;
  }
  .card {
    width: 540px;
    height: 310px;
    position: relative;
    overflow: hidden;
    box-shadow: 0 10px 24px rgba(0,0,0,0.22);
  }

  /* Front */
  .card--front { background: var(--card-white); }
  .card--front .bottom-band {
    position: absolute; left: 0; right: 0; bottom: 0;
    height: 14px; background: var(--brand-blue);
  }
  .card--front .divider {
    position: absolute; left: 268px; top: 60px;
    width: 1px; height: 170px; background: var(--divider);
  }
  .brand-block {
    position: absolute; left: 34px; top: 96px; width: 210px;
  }
  .brand-name {
    display: flex; align-items: flex-start; gap: 8px;
    color: var(--brand-blue);
    font-weight: 700; font-size: 21px; line-height: 1.15;
  }
  .brand-name .mark {
    flex: none; width: 12px; height: 12px; margin-top: 6px;
    background: var(--brand-blue);
  }
  .brand-tagline {
    margin-top: 12px; padding-top: 6px;
    border-top: 1px solid var(--brand-blue);
    color: var(--brand-blue);
    font-size: 11px; font-weight: 500;
  }
  .contact-block {
    position: absolute; left: 296px; top: 78px;
  }
  .person-name {
    color: var(--brand-blue); font-weight: 700; font-size: 19px;
    letter-spacing: 0.2px;
  }
  .person-role {
    color: var(--ink); font-size: 12px; margin-top: 2px;
  }
  .contact-list { list-style: none; margin-top: 20px; }
  .contact-list li {
    display: flex; align-items: center; gap: 8px;
    color: var(--ink); font-size: 11px; line-height: 1; margin-bottom: 8px;
  }
  .contact-list svg { width: 11px; height: 11px; flex: none; fill: var(--brand-blue); }

  /* Back */
  .card--back {
    background: var(--brand-blue-deep);
    color: var(--card-white);
    display: flex; flex-direction: column; align-items: center;
  }
  .back-brand {
    margin-top: 92px;
    display: flex; align-items: center; gap: 12px;
    font-weight: 700; font-size: 24px; text-align: center;
  }
  .back-brand .mark { width: 14px; height: 14px; background: var(--card-white); }
  .services {
    margin-top: auto; margin-bottom: 36px;
    text-align: center; font-size: 11.5px; line-height: 1.5;
  }
  .services .sep { display: inline-block; margin: 0 6px; opacity: 0.9; }
</style>
</head>
<body>

  <section class="card card--front" aria-label="Business card front">
    <div class="brand-block">
      <div class="brand-name"><span class="mark"></span><span>Stonebridge Building and Projects</span></div>
      <div class="brand-tagline">Built right, built to last</div>
    </div>

    <div class="divider"></div>

    <div class="contact-block">
      <h1 class="person-name">OMAR HADDANI</h1>
      <p class="person-role">Director</p>
      <ul class="contact-list">
        <li>
          <svg viewBox="0 0 24 24" aria-hidden="true"><path d="M6.6 10.8a15.1 15.1 0 0 0 6.6 6.6l2.2-2.2a1 1 0 0 1 1-.25 11.4 11.4 0 0 0 3.6.57 1 1 0 0 1 1 1V20a1 1 0 0 1-1 1A17 17 0 0 1 3 4a1 1 0 0 1 1-1h3.5a1 1 0 0 1 1 1c0 1.25.2 2.45.57 3.57a1 1 0 0 1-.25 1z"/></svg>
          369-240-1187
        </li>
        <li>
          <svg viewBox="0 0 24 24" aria-hidden="true"><path d="M2 5h20v14H2z M3.5 6.5 12 13l8.5-6.5" stroke="#fff" stroke-width="1.6"/></svg>
          omar@sbpbuilding.com.au
        </li>
        <li>
          <svg viewBox="0 0 24 24" aria-hidden="true"><circle cx="12" cy="12" r="10"/><path d="M2 12h20M12 2c3 3 3 17 0 20M12 2c-3 3-3 17 0 20" stroke="#fff" stroke-width="1.4" fill="none"/></svg>
          www.sbpbuilding.com.au
        </li>
        <li>
          <svg viewBox="0 0 24 24" aria-hidden="true"><circle cx="12" cy="12" r="10"/></svg>
          sbp_building
        </li>
      </ul>
    </div>

    <div class="bottom-band"></div>
  </section>

  <section class="card card--back" aria-label="Business card back">
    <div class="back-brand"><span class="mark"></span><span>Stonebridge Building<br>and Projects</span></div>
    <p class="services">
      Home improvement projects<span class="sep">::</span>House renovations<span class="sep">::</span>House extensions<br>
      Bathroom &amp; kitchen renovations<span class="sep">::</span>New builds &amp; granny flats
    </p>
  </section>

</body>
</html>
```